KLV Plant Services

We are a heavy diesel mechanical business with additional air con certificates, remapping engine rebuilt

Contact Information for Business Card

Company Name, Director Name, Managing Director, Contact details, email and website

Font styles to use
Serif
Script

```html
<!DOCTYPE html>
<html lang="en">
<head>
<meta charset="utf-8">
<title>KLV Plant Services – Business Card</title>
<link href="https://fonts.googleapis.com/css2?family=Noto+Serif:wght@400;700&display=swap" rel="stylesheet">
<style>
  :root {
    --backdrop: #3c3c3c;
    --backdrop-dark: #1e1e1e;
    --card: #ffffff;
    --navy: #2b2a78;
    --ink: #2a2a2a;
    --muted: #444444;
  }
  * { margin: 0; padding: 0; box-sizing: border-box; }
  html, body {
    width: 1200px;
    height: 780px;
    overflow: hidden;
  }
  body {
    background: radial-gradient(ellipse at 30% 20%, var(--backdrop), var(--backdrop-dark));
    font-family: "Noto Serif", Georgia, serif;
    display: flex;
    align-items: center;
    justify-content: center;
    gap: 44px;
  }
  .card {
    position: relative;
    width: 540px;
    height: 330px;
    background: var(--card);
    border-radius: 22px;
    overflow: hidden;
    box-shadow: 0 18px 40px rgba(0,0,0,0.45);
  }

  /* Wordmark */
  .wordmark {
    display: flex;
    align-items: center;
    gap: 12px;
    color: var(--navy);
    font-weight: 700;
    white-space: nowrap;
  }
  .wordmark__dot {
    flex: none;
    border-radius: 50%;
    background: var(--navy);
  }

  /* Back: contact side */
  .card--contact .wordmark {
    position: absolute;
    top: 34px;
    left: 34px;
    font-size: 22px;
    gap: 9px;
  }
  .card--contact .wordmark__dot { width: 16px; height: 16px; }

  .address {
    position: absolute;
    top: 92px;
    left: 70px;
    font-size: 14px;
    line-height: 1.45;
    color: var(--muted);
  }
  .contact-list {
    position: absolute;
    top: 150px;
    left: 34px;
    list-style: none;
    font-size: 14px;
    line-height: 1.6;
    color: var(--ink);
  }
  .contact-list li {
    display: flex;
    align-items: center;
    gap: 8px;
  }
  .contact-list svg { width: 13px; height: 13px; flex: none; }

  .person {
    position: absolute;
    top: 150px;
    right: 40px;
    text-align: right;
  }
  .person__name {
    font-size: 21px;
    font-weight: 700;
    letter-spacing: 0.5px;
    color: var(--navy);
    text-transform: uppercase;
  }
  .person__role {
    font-size: 15px;
    color: var(--navy);
    margin-top: 2px;
  }
  .accent-band {
    position: absolute;
    top: 150px;
    right: 0;
    width: 14px;
    height: 62px;
    background: var(--navy);
  }

  /* Front: brand side */
  .card--brand {
    display: flex;
    align-items: center;
    justify-content: center;
  }
  .card--brand .wordmark { font-size: 40px; }
  .card--brand .wordmark__dot { width: 34px; height: 34px; }
</style>
</head>
<body>

  <section class="card card--contact" aria-label="Business card, contact side">
    <div class="wordmark">
      <span class="wordmark__dot"></span>
      <span class="wordmark__name">KLV Plant Services</span>
    </div>

    <p class="address">Your address, City<br>State, Zip 1234</p>

    <ul class="contact-list">
      <li>
        <svg viewBox="0 0 16 16" aria-hidden="true"><path fill="var(--navy)" d="M3.6 1.2l2.3 2.6-1.2 1.8c.9 2 2.6 3.7 4.6 4.6l1.8-1.2 2.6 2.3-1.3 2.5C7 13.6 2.4 9 1.2 3.3z"/></svg>
        123 456 789
      </li>
      <li>
        <svg viewBox="0 0 16 16" aria-hidden="true"><rect x="1" y="3" width="14" height="10" rx="1.5" fill="var(--navy)"/><path d="M1.5 4l6.5 5 6.5-5" fill="none" stroke="#fff" stroke-width="1.3"/></svg>
        info@yourgmail.com
      </li>
      <li>
        <svg viewBox="0 0 16 16" aria-hidden="true"><circle cx="8" cy="8" r="7" fill="var(--navy)"/><path d="M1 8h14M8 1c-3 3.5-3 10.5 0 14M8 1c3 3.5 3 10.5 0 14" fill="none" stroke="#fff" stroke-width="1"/></svg>
        www.yourwebsite.com
      </li>
    </ul>

    <div class="person">
      <p class="person__name">Daniel Carter</p>
      <p class="person__role">Managing Director</p>
    </div>
    <div class="accent-band"></div>
  </section>

  <section class="card card--brand" aria-label="Business card, brand side">
    <div class="wordmark">
      <span class="wordmark__dot"></span>
      <span class="wordmark__name">KLV Plant Services</span>
    </div>
  </section>

</body>
</html>
```